Advanced Therapeutic Massage Therapist

I need a business card advertising my massage services as an advanced therapeutic massage therapist. I offer advanced therapeutic massage, swedish and deep tissue. I want to create a simple, professional and feminine card. I like bright colours and creativity.

I prefer a bold and experimental approach rather than something status-quo. A card to suggest therapeutic healing through dynamic massage. Motifs, shapes or layout which suggest movement and flow.
Updates

Target Market(s)

Everybody!

Industry/Entity Type

Health And Wellness

Contact Information for Business Card

The card should include:
My name, logo, services offered and my contact details.

Sláine Dunleavy
Massage Therapist

- Swedish - Deep Tissue - Advanced Therapeutic

Phone: (+353) 87 216 4093
Email: regenerate@slainedunleavy-example.com
Website: www.slainedunlevy-example.com

Font styles to use
Serif
Sans Serif
Decorative
Script

Colors

Designer to choose colors to be used in the design.

Requirements
Must have
• An example may contain something like this, yet concise:
• "Sláine Dunleavy
• Massage Therapist
• - Swedish - Deep Tissue - Advanced Therapeutic"
Nice to have
• This sentence is optional:
• Imagery such as a logo or symbol. I have attached a file containing a logo I had produced however the name is incorrect now as it is "Sláine" not "Nelly". It could be edited to change it to Sláine.
• I have sent the file as .psd .jpg. .pdf and .png
• I like when the card conveys energy, movement, pressure points, flow etc.
• I just like the designer to follow their own style and ideas. I like bright colours but must have a lot of a base colour to offset it. I really prefer them to follow their own inspiration. That is my preference.
Should not have
• Pine trees, non-native trees to Britain and Ireland, exotic flowers or animals that are not native to Britain and Ireland.
• I don't like brown as the background colour of the card.
• The cars shouldn't look like a wedding invitation i.e too many floral type designs.

```html
<!DOCTYPE html>
<html lang="en">
<head>
<meta charset="utf-8">
<title>Sláine Dunleavy – Massage Therapist Business Card</title>
<link href="https://fonts.googleapis.com/css2?family=Great+Vibes&family=Questrial&display=swap" rel="stylesheet">
<style>
  :root {
    --stage: #6a6a6a;
    --mint-light: #cdeee3;
    --mint: #a9e2d2;
    --mint-deep: #86d1bd;
    --charcoal: #232323;
    --charcoal-soft: #2b2b2b;
    --ink: #3a3f3e;
    --white: #f4f4f2;
    --gold: #c9a04a;
    --gold-deep: #8f6a28;
    --teal-text: #6fbf9c;
  }
  * { margin: 0; padding: 0; box-sizing: border-box; }
  html, body { width: 1200px; height: 550px; overflow: hidden; }
  body {
    background: var(--stage);
    position: relative;
    font-family: "Questrial", "Century Gothic", sans-serif;
  }
  .card {
    position: absolute;
    top: 157px;
    width: 390px;
    height: 236px;
    overflow: hidden;
  }
  .card--front {
    left: 195px;
    background:
      radial-gradient(ellipse at 20% 25%, var(--mint-light) 0%, transparent 55%),
      radial-gradient(ellipse at 80% 75%, var(--mint-deep) 0%, transparent 50%),
      var(--mint);
  }
  .card--back {
    left: 614px;
    background: radial-gradient(ellipse at 50% 40%, var(--charcoal-soft), var(--charcoal));
    border-top: 1px solid #d8d8d8;
  }
  .emblem {
    position: absolute;
    border-radius: 50%;
    border: 2px solid var(--gold);
    background: radial-gradient(circle, var(--mint-light) 0%, var(--mint) 100%);
    display: flex;
    align-items: center;
    justify-content: center;
  }
  .emblem__name {
    font-family: "Questrial", sans-serif;
    color: var(--gold-deep);
    font-size: 13px;
    letter-spacing: 1.5px;
  }
  .card--front .emblem { width: 112px; height: 112px; left: 139px; top: 42px; }
  .card--back .emblem { width: 108px; height: 108px; left: 41px; top: 58px; }
  .card__name {
    position: absolute;
    font-family: "Great Vibes", cursive;
    font-weight: 400;
    line-height: 1.2;
    white-space: nowrap;
  }
  .card__role {
    position: absolute;
    font-size: 9.5px;
    line-height: 1.2;
    letter-spacing: 1.4px;
    white-space: nowrap;
  }
  .card--front .card__name {
    left: 0; width: 100%; text-align: center;
    top: 160px; font-size: 22px; color: var(--ink);
  }
  .card--front .card__role {
    left: 0; width: 100%; text-align: center; padding-left: 10px;
    top: 186px; color: var(--ink);
  }
  .divider {
    position: absolute;
    left: 173px; top: 53px;
    width: 1.5px; height: 118px;
    background: linear-gradient(to bottom, transparent, var(--gold) 15%, var(--gold) 85%, transparent);
  }
  .card--back .card__name { left: 196px; top: 60px; font-size: 24px; color: var(--white); }
  .card--back .card__role { left: 202px; top: 89px; color: var(--white); }
  .contact-list {
    position: absolute;
    left: 202px; top: 112px;
    list-style: none;
  }
  .contact-list li {
    display: flex;
    align-items: center;
    height: 17px;
    font-size: 10.5px;
    color: var(--white);
    white-space: nowrap;
  }
  .contact-list svg { width: 9px; height: 9px; margin-right: 11px; fill: var(--white); flex: none; }
  .services {
    position: absolute;
    left: 0; width: 100%;
    top: 210px;
    text-align: center;
    font-size: 10.5px;
    color: var(--teal-text);
    white-space: nowrap;
  }
</style>
</head>
<body>

  <section class="card card--front" aria-label="Card front">
    <div class="emblem" role="img" aria-label="Logo area"><span class="emblem__name">Dunleavy</span></div>
    <h1 class="card__name">Sláine Dunleavy</h1>
    <p class="card__role">massage therapist</p>
  </section>

  <section class="card card--back" aria-label="Card back">
    <div class="emblem" role="img" aria-label="Logo area"><span class="emblem__name">Dunleavy</span></div>
    <div class="divider"></div>
    <h2 class="card__name">Sláine Dunleavy</h2>
    <p class="card__role">massage therapist</p>
    <ul class="contact-list">
      <li>
        <svg viewBox="0 0 10 10" aria-hidden="true"><path d="M1 3.5C1 2 2.5 1.5 5 1.5S9 2 9 3.5L7.5 4.2 7 3.2H3L2.5 4.2ZM2.5 5h5l1 3.5h-7Z"/></svg>
        (+353) 87 216 4093
      </li>
      <li>
        <svg viewBox="0 0 10 10" aria-hidden="true"><path d="M1 2.5h8v5H1Z"/><path d="M1.2 2.7 5 5.6 8.8 2.7" stroke="#232323" stroke-width="0.8" fill="none"/></svg>
        slaine@dunleavy-example.com
      </li>
      <li>
        <svg viewBox="0 0 10 10" aria-hidden="true"><circle cx="5" cy="5" r="4"/><path d="M1 5h8M5 1v8M2 3h6M2 7h6" stroke="#232323" stroke-width="0.6" fill="none"/></svg>
        www.slainedunlevy-example.com
      </li>
    </ul>
    <p class="services">Swedish - Deep Tissue - Advanced Therapeutic</p>
  </section>

</body>
</html>
```